Commercial Post Cards

We are looking for 3 postcards that are similar but target 3 commercial property types. they will be 6x9 cards can be front and back or not.
1. Hotel Postcard – Taviqon / Bed Bug Protection
Use the attached Taviqon sample as the primary direction.
The focus should be:
Proactive bed bug prevention and control
Protecting guests and the hotel's reputation
Regular inspections
Documentation and risk management
Professional commercial pest management
The backside should transition into our General Pest Control services, showing that we can be the hotel's complete pest management provider beyond just bed bugs.
2. Apartment Complex Postcard
Target apartment owners, property managers, and management companies.
Focus on:
General pest control
Bed bug control
Rodent control
Preventative pest management
Protecting residents and the property
Reliable, ongoing service and documentation
The message should position us as a full-service pest management partner for multifamily properties.

3. Commercial Building Postcard
Target office buildings, banks, storage facilities, and other commercial properties.

Focus on:
General commercial pest control
Rodent control
Fly management
Recurring service programs
Protecting the property, employees, customers, and reputation

Overall Direction
All three postcards should have a consistent brand and visual style, but each should feel specifically designed for its target market.

We want the messaging to communicate:
Professional • Reliable • Proactive • Locally Owned & Operated • Serving Since 2017

The goal is not to overwhelm the reader with information. These should be marketing pieces that quickly communicate the problem we solve, our expertise, and why a commercial property should contact us.

I have included some of our marketing materials for help with what we do.

```html
<!DOCTYPE html>
<html lang="en">
<head>
<meta charset="utf-8">
<title>Taviqon Hotel Postcard</title>
<link rel="stylesheet" href="https://fonts.googleapis.com/css2?family=Bebas+Neue&family=Arimo:wght@700&display=swap">
<style>
  :root {
    --orange: #fa5215;
    --ink: #2b2b2b;
    --dark: #222223;
    --white: #ffffff;
    --room-light: #efe9e2;
    --room-mid: #cdbfae;
    --room-dark: #6b5a48;
  }
  * { margin: 0; padding: 0; box-sizing: border-box; }
  html, body { width: 1200px; height: 800px; overflow: hidden; background: var(--white); }
  .postcard { position: relative; width: 1200px; height: 800px; background: var(--white); font-family: "Arimo", Arial, sans-serif; color: var(--ink); overflow: hidden; }

  .room-photo {
    position: absolute; left: 400px; top: 0; width: 800px; height: 360px;
    background: linear-gradient(90deg, var(--white) 0%, rgba(255,255,255,0) 22%),
                linear-gradient(160deg, var(--room-light) 0%, var(--room-mid) 45%, var(--room-dark) 100%);
  }

  .brand { position: absolute; left: 40px; top: 62px; display: flex; align-items: center; gap: 12px; }
  .brand-mark { width: 30px; height: 30px; background: var(--orange); }
  .brand-name { font-family: "Arimo", Arial, sans-serif; font-weight: 700; font-size: 38px; color: var(--orange); letter-spacing: -0.5px; }

  .headline { position: absolute; left: 38px; top: 168px; font-family: "Bebas Neue", Impact, sans-serif; font-size: 132px; line-height: 1; color: var(--ink); letter-spacing: 1px; }
  .headline .accent { color: var(--orange); }
  .subhead { position: absolute; left: 40px; top: 284px; font-size: 28px; line-height: 33px; color: var(--ink); }

  .tagline-band { position: absolute; left: 0; top: 360px; width: 1200px; height: 53px; background: var(--orange); border-bottom: 5px solid var(--dark); box-sizing: content-box; }
  .tagline-band p { position: absolute; left: 118px; top: 16px; font-size: 17.5px; color: var(--white); white-space: nowrap; }
  .band-shield { position: absolute; left: 38px; top: 346px; width: 70px; height: 80px; }

  .slogan { position: absolute; left: 38px; top: 442px; font-family: "Bebas Neue", Impact, sans-serif; font-size: 112px; line-height: 96px; color: var(--ink); }
  .slogan .accent { color: var(--orange); }

  .benefits { position: absolute; top: 442px; list-style: none; }
  .benefits li { position: relative; padding-left: 48px; font-size: 21px; line-height: 25px; color: var(--ink); }
  .benefits li svg { position: absolute; left: 0; top: 0; width: 36px; height: 40px; }
  .benefits.col-a { left: 590px; width: 300px; }
  .benefits.col-b { left: 903px; width: 290px; }
  .col-a li:nth-child(1) { margin-top: 10px; }
  .col-a li:nth-child(2) { margin-top: 12px; }
  .col-a li:nth-child(3) { margin-top: 17px; }
  .col-b li:nth-child(1) { margin-top: 10px; }
  .col-b li:nth-child(2) { margin-top: 15px; }

  .footer { position: absolute; left: 0; top: 684px; width: 1200px; height: 116px; background: var(--dark); }
  .cta { position: absolute; left: 262px; top: 668px; width: 720px; height: 48px; border: 3px solid var(--orange); border-radius: 0 16px 16px 0; background: var(--white); overflow: hidden; }
  .cta-lead { position: absolute; left: 0; top: 0; height: 100%; width: 430px; background: var(--orange); clip-path: polygon(0 0, 410px 0, 430px 50%, 410px 100%, 0 100%); }
  .cta-lead span, .cta-tail { position: absolute; top: 9px; font-size: 23px; white-space: nowrap; }
  .cta-lead span { left: 36px; color: var(--white); }
  .cta-tail { left: 438px; color: var(--ink); }
  .cta-shield { position: absolute; left: 218px; top: 646px; width: 72px; height: 84px; }

  .contact { position: absolute; top: 738px; font-size: 33px; color: var(--white); display: flex; align-items: center; gap: 20px; }
  .contact svg { width: 28px; height: 28px; }
  .contact.phone { left: 292px; }
  .contact.web { left: 640px; }
  .divider { position: absolute; left: 599px; top: 732px; width: 2px; height: 46px; background: var(--white); }
</style>
</head>
<body>
<main class="postcard">
  <div class="room-photo" role="img" aria-label="Bright, tidy hotel room with a made double bed, armchair, side table and curtained window"></div>

  <header class="brand">
    <span class="brand-mark"></span>
    <span class="brand-name">Brisko Pest Control</span>
  </header>

  <h1 class="headline">TAVI<span class="accent">QON</span></h1>
  <p class="subhead">Quarterly Inspected &amp; Documented<br>Bed Bug Prevention for Hotels</p>

  <div class="tagline-band">
    <p>Proactive protection. Quarterly inspected. Documented results. Peace of mind for your guests and your business.</p>
  </div>
  <svg class="band-shield" viewBox="0 0 70 80" aria-hidden="true">
    <path d="M35 2 L67 14 V40 C67 60 52 72 35 78 C18 72 3 60 3 40 V14 Z" fill="var(--orange)"/>
    <path d="M35 9 L60 18 V40 C60 56 49 66 35 71 C21 66 10 56 10 40 V18 Z" fill="var(--white)"/>
    <circle cx="35" cy="42" r="9" fill="var(--ink)"/>
  </svg>

  <h2 class="slogan">DON’T LET BED<br>BUGS <span class="accent">CHECK IN.</span></h2>

  <ul class="benefits col-a">
    <li><svg viewBox="0 0 36 40"><path d="M18 1 L34 7 V20 C34 30 27 36 18 39 C9 36 2 30 2 20 V7 Z" fill="var(--orange)"/><path d="M18 5 L30 10 V20 C30 28 25 32 18 35 C11 32 6 28 6 20 V10 Z" fill="var(--ink)"/><path d="M11 20 L16 25 L25 15" stroke="var(--white)" stroke-width="3" fill="none"/></svg>Proactive bed bug prevention and control</li>
    <li><svg viewBox="0 0 36 40"><path d="M18 1 L34 7 V20 C34 30 27 36 18 39 C9 36 2 30 2 20 V7 Z" fill="var(--orange)"/><path d="M18 5 L30 10 V20 C30 28 25 32 18 35 C11 32 6 28 6 20 V10 Z" fill="var(--ink)"/><path d="M11 20 L16 25 L25 15" stroke="var(--white)" stroke-width="3" fill="none"/></svg>Protecting guests and the hotel's reputation</li>
    <li><svg viewBox="0 0 36 40"><path d="M18 1 L34 7 V20 C34 30 27 36 18 39 C9 36 2 30 2 20 V7 Z" fill="var(--orange)"/><path d="M18 5 L30 10 V20 C30 28 25 32 18 35 C11 32 6 28 6 20 V10 Z" fill="var(--ink)"/><path d="M11 20 L16 25 L25 15" stroke="var(--white)" stroke-width="3" fill="none"/></svg>Regular inspections</li>
  </ul>
  <ul class="benefits col-b">
    <li><svg viewBox="0 0 36 40"><path d="M18 1 L34 7 V20 C34 30 27 36 18 39 C9 36 2 30 2 20 V7 Z" fill="var(--orange)"/><path d="M18 5 L30 10 V20 C30 28 25 32 18 35 C11 32 6 28 6 20 V10 Z" fill="var(--ink)"/><path d="M11 20 L16 25 L25 15" stroke="var(--white)" stroke-width="3" fill="none"/></svg>Documentation and risk management</li>
    <li><svg viewBox="0 0 36 40"><path d="M18 1 L34 7 V20 C34 30 27 36 18 39 C9 36 2 30 2 20 V7 Z" fill="var(--orange)"/><path d="M18 5 L30 10 V20 C30 28 25 32 18 35 C11 32 6 28 6 20 V10 Z" fill="var(--ink)"/><path d="M11 20 L16 25 L25 15" stroke="var(--white)" stroke-width="3" fill="none"/></svg>Professional commercial pest management</li>
  </ul>

  <footer class="footer"></footer>
  <div class="cta">
    <div class="cta-lead"><span>ASK US FOR A CUSTOM QUOTE</span></div>
    <span class="cta-tail">FOR YOUR PROPERTY.</span>
  </div>
  <svg class="cta-shield" viewBox="0 0 72 84" aria-hidden="true">
    <path d="M36 2 L70 14 V42 C70 63 55 76 36 82 C17 76 2 63 2 42 V14 Z" fill="var(--orange)"/>
    <path d="M36 8 L63 18 V42 C63 59 51 69 36 74 C21 69 9 59 9 42 V18 Z" fill="var(--white)"/>
    <path d="M36 13 L58 21 V42 C58 56 48 64 36 68 C24 64 14 56 14 42 V21 Z" fill="var(--ink)"/>
    <rect x="22" y="28" width="20" height="16" rx="3" fill="none" stroke="var(--white)" stroke-width="2.5"/>
    <path d="M32 38 H50 V52 H44 L40 56 V52 H32 Z" fill="var(--white)" stroke="var(--ink)" stroke-width="1.5"/>
    <text x="32" y="40" font-family="Arimo, Arial, sans-serif" font-size="10" font-weight="700" fill="var(--white)" text-anchor="middle">?</text>
  </svg>

  <div class="contact phone">
    <svg viewBox="0 0 28 28" aria-hidden="true"><circle cx="14" cy="14" r="14" fill="var(--orange)"/><path d="M9 7 L12 7 L13 11 L11 12.5 C12 15 13.5 16.5 15.5 17 L17 15 L21 16 V19 C21 20 20 21 19 21 C13 20.5 8 15.5 7.5 9 C7.5 8 8 7 9 7 Z" fill="var(--white)"/></svg>
    <span>208-555-0147</span>
  </div>
  <div class="divider"></div>
  <div class="contact web">
    <svg viewBox="0 0 28 28" aria-hidden="true"><circle cx="14" cy="14" r="14" fill="var(--orange)"/><path d="M20 8 L7 13 L12 15 L14 20 Z" fill="var(--white)"/></svg>
    <span>www.briskopest.com</span>
  </div>
</main>
</body>
</html>
```